NZ First of it's kind solutions directory and marketplace for busy Mums needs a business card design

We need a business card design for our new nationwide business in NZ (long term plans to go global). We provide solutions to the everyday challenges that busy Mums face by connecting them with quality communities and suppliers of carefully selected, relevant products and services. We sell direct via our online marketplace. The final design should communicate our values of inclusivity, quality and smart solutions. Colours should incorporate our logo colour palette of #477077 and #6ba8b2. Our website is at https://www.brightnestmums.example

Target Market(s)

busy Mums, Age 28 – 50, female, income over $100K, location main centres NZ primarily but NZ wide. Is likely juggling work or career with a young family. Probably had hobbies which have fallen by the wayside.
-Wants to succeed in her chosen career without compromising on family life
-to successfully juggle her career without feeling like she is compromising her children
- Is time poor, something always has to give and it’s generally her health (she’ll stay up late, get stressed)
- probably ex corporate or professional career. Has discretional income

Industry/Entity Type

Business

Contact Information for Business Card

Lena Forbisher, Founder, BrightNestMums.example (Strapline Tap; Gather; Sorted), 47 Kowhai Terrace, Ellerslie, Auckland 1051, New Zealand. Mob: 021 483 517 Ph: +64 (0)9 571 4860

Font styles to use
Other font styles liked:
• Raleway, and/or Architects Daughter

Colors
00a990
33b8a4
86cfc6
cfeae6

Requirements
Must have
• the above details, streamline. the logo and colours associated with those logos
Should not have
• foil or metallic colours

```html
<!DOCTYPE html>
<html lang="en">
<head>
<meta charset="utf-8">
<title>BrightNestMums — Business Card</title>
<link rel="stylesheet" href="https://fonts.googleapis.com/css2?family=Roboto:wght@400;500&family=Roboto+Condensed:wght@400;700&display=swap">
<style>
  :root {
    --backdrop: #2a2a2b;
    --card: #f1f1f1;
    --brand-dark: #477077;
    --brand-light: #6ba8b2;
    --ink-white: #ffffff;
    --ink-grey: #4a4a4a;
  }
  * { margin: 0; padding: 0; box-sizing: border-box; }
  html, body { width: 1200px; height: 960px; overflow: hidden; }
  body {
    background: var(--backdrop);
    position: relative;
    font-family: "Roboto", Arial, sans-serif;
  }
  .card {
    position: absolute;
    width: 600px;
    height: 343px;
    border-radius: 22px;
    background: var(--card);
    overflow: hidden;
  }
  .card--front { left: 314px; top: 113px; }
  .card--back { left: 311px; top: 472px; }

  .front-swoosh { position: absolute; inset: 0; width: 600px; height: 343px; }

  .identity {
    position: absolute;
    right: 43px;
    top: 48px;
    text-align: right;
    color: var(--ink-white);
    font-family: "Roboto Condensed", Arial, sans-serif;
  }
  .identity__name { font-size: 23px; font-weight: 700; line-height: 1.1; }
  .identity__role { font-size: 17px; font-weight: 400; line-height: 1.1; }

  .contact {
    position: absolute;
    right: 43px;
    top: 198px;
    text-align: right;
    color: var(--ink-white);
    font-size: 15px;
    line-height: 19px;
  }
  .contact__address { margin-bottom: 7px; }
  .contact__line { display: flex; justify-content: flex-end; align-items: center; gap: 6px; height: 19.5px; }
  .contact__icon { width: 14px; height: 14px; flex: none; }

  .brand {
    position: absolute;
    left: 46px;
    top: 258px;
    display: flex;
    align-items: center;
    gap: 10px;
  }
  .brand__dot { width: 28px; height: 28px; border-radius: 50%; background: var(--brand-dark); }
  .brand__name { font-size: 27px; font-weight: 500; color: var(--brand-dark); letter-spacing: -0.3px; }

  .back-mark {
    position: absolute;
    left: 50%;
    top: 92px;
    transform: translateX(-50%);
    display: flex;
    flex-direction: column;
    align-items: center;
    gap: 14px;
  }
  .back-mark__dot { width: 110px; height: 110px; border-radius: 50%; background: var(--brand-dark); }
  .back-mark__name { font-size: 22px; font-weight: 500; color: var(--brand-dark); }
  .strapline {
    position: absolute;
    left: 0; right: 0;
    top: 286px;
    text-align: center;
    font-size: 15px;
    color: var(--ink-grey);
  }
</style>
</head>
<body>
  <section class="card card--front" aria-label="Business card front">
    <svg class="front-swoosh" viewBox="0 0 600 343" aria-hidden="true">
      <path d="M322 0 C250 40 228 185 376 343 L600 343 L600 0 Z" fill="var(--brand-dark)"/>
      <path d="M346 0 C268 40 250 185 391 343 L600 343 L600 0 Z" fill="var(--brand-light)" stroke="#ffffff" stroke-width="2"/>
    </svg>

    <div class="identity">
      <div class="identity__name">LENA FORBISHER</div>
      <div class="identity__role">FOUNDER</div>
    </div>

    <div class="contact">
      <div class="contact__address">47 Kowhai Terrace, Ellerslie<br>Auckland 1051, New Zealand.</div>
      <div class="contact__line">+64 (0)9 571 4860
        <svg class="contact__icon" viewBox="0 0 14 14" aria-hidden="true"><path d="M3 1 L5 1 L6 4 L4.5 5.2 C5.3 7 7 8.7 8.8 9.5 L10 8 L13 9 L13 11 C13 12 12 13 11 13 C6 12.5 1.5 8 1 3 C1 2 2 1 3 1 Z" fill="#fff"/></svg>
      </div>
      <div class="contact__line">021 483 517
        <svg class="contact__icon" viewBox="0 0 14 14" aria-hidden="true"><rect x="3.5" y="0.8" width="7" height="12.4" rx="1.2" fill="none" stroke="#fff" stroke-width="1.4"/><circle cx="7" cy="11" r="0.8" fill="#fff"/></svg>
      </div>
      <div class="contact__line">BrightNestMums.example
        <svg class="contact__icon" viewBox="0 0 14 14" aria-hidden="true"><circle cx="7" cy="7" r="6" fill="#fff"/><path d="M4 3.5 C5.5 4.5 5 6 6.5 6.5 C7.5 7 6.5 9 7.5 10.5 M9 2.5 C8.5 4 10 4.5 11.5 5" stroke="var(--brand-light)" stroke-width="1.4" fill="none"/></svg>
      </div>
    </div>

    <div class="brand">
      <span class="brand__dot" aria-hidden="true"></span>
      <span class="brand__name">BrightNestMums</span>
    </div>
  </section>

  <section class="card card--back" aria-label="Business card back">
    <div class="back-mark">
      <span class="back-mark__dot" aria-hidden="true"></span>
      <span class="back-mark__name">BrightNestMums</span>
    </div>
    <p class="strapline">Tap; Gather; Sorted</p>
  </section>
</body>
</html>
```